New National Dermatology Group needs a business card!

We need a business card for our new national company that has 3 brands within the business:
Lumora Clinics Australia, Tessaly Clinics Australia and Corvane Clinics Australia.
We help people access dermatology services close to home throughout Australia.
We need a business card that has:
all 3 logos on it,
Our websites (there are three, listed above)
Our email (there are three, listed above)
The location of our first clinic: 41 Willow Rd Parramatta (this can then be changed for each location as required)

```html
<!DOCTYPE html>
<html lang="en">
<head>
<meta charset="utf-8">
<title>Dermatology Group Business Card</title>
<link href="https://fonts.googleapis.com/css2?family=Cinzel:wght@600&family=Arimo:wght@400&display=swap" rel="stylesheet">
<style>
  :root {
    --bg: #1c1c1c;
    --card-white: #ffffff;
    --ink: #111111;
    --brand-brown: #7a3a12;
    --brand-green: #1eaa4a;
    --brand-orange: #f08a24;
    --grad-green: #1fae4b;
    --grad-orange: #f3801f;
    --grad-brown: #8a3a14;
    --headline: #ffffff;
  }
  * { box-sizing: border-box; margin: 0; padding: 0; }
  html, body {
    width: 1200px; height: 1108px; overflow: hidden;
    background: var(--bg);
  }
  .sheet {
    position: relative; width: 1200px; height: 1108px;
    display: flex; justify-content: center; align-items: center; gap: 80px;
  }
  .card {
    width: 440px; height: 770px; border-radius: 26px; overflow: hidden;
    position: relative;
  }
  .card-front {
    background: var(--card-white);
    display: flex; flex-direction: column; justify-content: center; gap: 46px;
    padding: 40px 30px;
  }
  .brand-block { text-align: center; }
  .brand-name {
    font-family: "Cinzel", serif; font-weight: 600;
    font-size: 27px; letter-spacing: 1px; line-height: 1.2;
    padding-bottom: 14px;
  }
  .brand-block--corvane .brand-name, .brand-block--corvane .site-name { color: var(--brand-brown); }
  .brand-block--lumora .brand-name, .brand-block--lumora .site-name { color: var(--brand-green); }
  .brand-block--tessaly .brand-name, .brand-block--tessaly .site-name { color: var(--brand-orange); }
  .contact {
    font-family: "Arimo", sans-serif; font-size: 20px; color: var(--ink);
    line-height: 1.45; list-style: none;
  }
  .card-back {
    background:
      radial-gradient(ellipse at 100% 0%, var(--grad-orange) 0%, rgba(243,128,31,0) 45%),
      radial-gradient(ellipse at 0% 100%, var(--grad-brown) 0%, rgba(138,58,20,0) 45%),
      var(--grad-green);
  }
  .back-headline {
    position: absolute; left: 50%; top: 50%;
    transform: translate(-50%, -50%) rotate(-60deg);
    white-space: nowrap;
    font-family: "Cinzel", serif; font-weight: 600;
    font-size: 34px; letter-spacing: 3px; color: var(--headline);
  }
</style>
</head>
<body>
<main class="sheet">
  <section class="card card-front" aria-label="Card front">
    <div class="brand-block brand-block--corvane">
      <p class="brand-name">Corvane Clinics Australia</p>
      <ul class="contact">
        <li>info@webname.com</li>
        <li>www.<span class="site-name">websitename</span>.com</li>
        <li>41 Willow Rd Parramatta</li>
      </ul>
    </div>
    <div class="brand-block brand-block--lumora">
      <p class="brand-name">Lumora Clinics Australia</p>
      <ul class="contact">
        <li>info@webname.com</li>
        <li>www.<span class="site-name">websitename</span>.com</li>
        <li>41 Willow Rd Parramatta</li>
      </ul>
    </div>
    <div class="brand-block brand-block--tessaly">
      <p class="brand-name">Tessaly Clinics Australia</p>
      <ul class="contact">
        <li>info@webname.com</li>
        <li>www.<span class="site-name">websitename</span>.com</li>
        <li>41 Willow Rd Parramatta</li>
      </ul>
    </div>
  </section>
  <section class="card card-back" role="img" aria-label="Card back: green gradient with orange and brown corners, faint repeated brand-name pattern">
    <p class="back-headline">CORVANE LUMORA TESSALY</p>
  </section>
</main>
</body>
</html>
```